Vensol Holdings Web Design

Vensol Holdings Limited Shenzhen

This project is a 10 page launch website.
Our client is seeking a contemporary homepage design for a Holdings company. Once we are happy with the homepage design and select designer we will request a secondary page design.

Please see attached company LOGO for an idea of style, it incorporates the traditional Chinese furniture lattice work. The Corvel crest website is one of our clients favorite so we would like to see a similar homepage design to this website.

Use the websites below for reference purpose. The first two are Chinese and the second two are international. We would like to see elements of both but more focus on international design.

http://www.evergrande.com/http://www.taurenfield.com/pub/default.aspx http://www.corvelcrest.com/zh/maldives_lorinhaven/
http://www.quelba-studio.com
http://media-cache-ex0.snapvalu.com/originals/71/a3/19/71a319c5b2d04e8f6a17c3b9e5d0f4a1.jpg

Company Background
VENSOL HOLDINGS, located in Qianhai, China, is a new real-estate project operator, structuring urban-rural real-estate investment and development, and industrial fund investment. The company also invests in supply chain management and supporting infrastructures. To create new spaces and livable cities Vensol Holdings develop win-win strategic partnerships with a number of institutions. Currently cooperating with Tianjing North Lumore, China urban and rural integrated demonstration.

Target Market(s)

B2B property investment. Target market customers are senior level management/decision makers of large corporations. Focusing geographically on the domestic market first and expanding internationally in 2nd and 3rd years.

Industry/Entity Type

Investment

Requirements
Must have
• Since this is a new company, we would like to the website representing growth and power, E.g. like a growing tree.
Should not have
• Low-level vectors such as curency symbols, American dollar.

```html
<!DOCTYPE html>
<html lang="en">
<head>
<meta charset="utf-8">
<title>Vensol Holdings</title>
<link rel="stylesheet" href="https://fonts.googleapis.com/css2?family=Arimo:wght@400;700&family=Open+Sans:wght@600;700&family=Roboto+Condensed:wght@300;400&display=swap">
<style>
:root{
  --black:#050505;
  --gold:#b8973e;
  --gold-text:#c9a44a;
  --band:#4b4b4b;
  --ink:#333333;
  --body:#444444;
  --white:#ffffff;
  --footer:#2b2b2b;
  --footer-text:#a9a9a9;
  --base:#1d1d1d;
  --field:#6b6b6b;
  --link:#2a8fd0;
}
*{box-sizing:border-box;margin:0;padding:0}
html,body{width:713px;height:1200px;overflow:hidden;background:var(--white)}
body{position:relative;font-family:Arimo,Arial,sans-serif;color:var(--body)}
.abs{position:absolute}

.site-header{left:0;top:0;width:713px;height:52px;background:var(--black)}
.brand{left:108px;top:4px;display:flex;align-items:center;gap:8px}
.brand-mark{width:44px;height:44px;border-radius:50%;border:1.5px solid var(--gold)}
.brand-name{font-family:"Roboto Condensed",sans-serif;font-size:11px;color:var(--gold-text);letter-spacing:.3px}
.nav{top:22px;font-size:7.5px;color:var(--white)}

.hero{left:0;top:52px;width:713px;height:299px;background:linear-gradient(180deg,#5a66a8 0%,#4b5592 45%,#2b2f4e 80%,#17182a 100%)}
.hero-title{left:0;top:130px;width:713px;text-align:center;font-family:"Open Sans",sans-serif;font-weight:700;font-size:17px;line-height:22px;color:var(--white)}
.hero-arrow{top:114px}

.cta-band{left:0;top:351px;width:713px;height:45px;background:var(--band)}
.cta-text{left:110px;top:18px;font-size:9.5px;color:var(--gold-text)}
.cta-button{left:488px;top:8px;width:118px;height:28px;background:var(--gold);color:var(--white);font-size:12px;text-align:center;line-height:28px}

.welcome{left:0;top:396px;width:713px;height:126px}
.section-title{font-family:"Roboto Condensed",sans-serif;font-weight:300;text-align:center;width:100%}
.welcome .section-title{top:29px;font-size:23px;color:var(--ink)}
.welcome-copy{left:115px;top:63px;width:483px;text-align:center;font-size:5.4px;line-height:10.5px;color:var(--body)}

.works{left:0;top:522px;width:713px;height:315px;background:linear-gradient(120deg,#2a2d33 0%,#3d4046 45%,#5b5a58 65%,#2c2e33 100%)}
.works .section-title{top:18px;font-size:15px;color:var(--white);font-weight:400}
.works-intro{left:107px;top:42px;width:500px;text-align:center;font-size:8px;line-height:16.5px;color:var(--white)}
.works-rule{left:107px;top:85px;width:499px;height:1px;background:#6d6f73}
.works-frame{left:107px;top:108px;width:278px;height:170px;background:var(--white);padding:4px}
.works-photo{width:100%;height:100%;background:linear-gradient(180deg,#7fb3e0 0%,#b9d7ec 50%,#7a8c95 85%,#5d6a70 100%)}
.slide-arrow{width:14px;height:16px;background:rgba(255,255,255,.9);border:1px solid #ddd}
.works-heading{left:416px;top:118px;font-family:"Roboto Condensed",sans-serif;font-size:15px;color:var(--white)}
.works-copy{left:418px;top:143px;width:182px;font-size:5.4px;line-height:10.4px;color:var(--white)}
.outline-button{left:418px;top:237px;width:153px;height:29px;border:1px solid var(--white);color:var(--white);font-family:"Roboto Condensed",sans-serif;font-size:13px;text-align:center;line-height:27px}

.feeds{left:0;top:837px;width:713px;height:196px}
.feed-icon{left:336px;top:33px;width:40px;height:40px;border-radius:50%;background:#2a9fd6}
.feeds .section-title{top:81px;font-size:23px;color:var(--ink);font-weight:400}
.feeds-copy{left:140px;top:115px;width:433px;text-align:center;font-size:7px;line-height:14.5px;color:var(--body)}
.feeds-link{left:0;top:148px;width:713px;text-align:center;font-size:7px;color:var(--link)}
.feed-arrow{top:92px;width:18px;height:18px;border:1px solid #e3e3e3}

.site-footer{left:0;top:1033px;width:713px;height:137px;background:var(--footer)}
.footer-title{top:15px;font-size:10px;color:#d8d8d8}
.footer-copy{font-size:5.3px;line-height:10.4px;color:var(--footer-text)}
.service-list{left:301px;top:34px;list-style:none;font-size:5.3px;line-height:14.3px;color:var(--footer-text)}
.field{left:468px;width:127px;background:var(--field);border-radius:2px;font-size:5.4px;color:var(--white);padding:5px 9px;font-weight:700}
.submit{left:554px;top:110px;width:41px;height:12px;background:var(--gold);border-radius:2px;color:var(--white);font-size:5px;text-align:center;line-height:12px}

.base-bar{left:0;top:1170px;width:713px;height:30px;background:var(--base)}
.copyright{left:109px;top:11px;font-size:5px;color:#9a9a9a}
.social{top:9px;width:12px;height:12px;border-radius:50%;background:#4a4a4a}
.base-code{left:646px;top:11px;font-size:6px;color:#9a9a9a}
</style>
</head>
<body>

<header class="site-header abs">
  <div class="brand abs">
    <span class="brand-mark"></span>
    <span class="brand-name">VENSOL HOLDINGS</span>
  </div>
  <nav>
    <span class="nav abs" style="left:328px">Home</span>
    <span class="nav abs" style="left:386px">About</span>
    <span class="nav abs" style="left:444px">Work</span>
    <span class="nav abs" style="left:500px">Services</span>
    <span class="nav abs" style="left:567px">Contact us</span>
  </nav>
</header>

<section class="hero abs" role="img" aria-label="Upward view of city skyscrapers against an evening sky">
  <h1 class="hero-title abs">VENSOL HOLDINGS, located in Qianhai, China, is a<br>new real-estate project operator</h1>
  <svg class="hero-arrow abs" style="left:55px" width="36" height="36" viewBox="0 0 36 36"><circle cx="18" cy="18" r="17" fill="none" stroke="rgba(255,255,255,.25)" stroke-width="1.5"/><path d="M21 11 L14 18 L21 25" fill="none" stroke="rgba(255,255,255,.3)" stroke-width="2"/></svg>
  <svg class="hero-arrow abs" style="left:622px" width="36" height="36" viewBox="0 0 36 36"><circle cx="18" cy="18" r="17" fill="none" stroke="rgba(255,255,255,.25)" stroke-width="1.5"/><path d="M15 11 L22 18 L15 25" fill="none" stroke="rgba(255,255,255,.3)" stroke-width="2"/></svg>
</section>

<section class="cta-band abs">
  <p class="cta-text abs">The company also invests in supply chain management and supporting infrastructures</p>
  <div class="cta-button abs">Get in Touch</div>
</section>

<section class="welcome abs">
  <h2 class="section-title abs">Welcome to&nbsp; Vensol Holdings</h2>
  <p class="welcome-copy abs">VENSOL HOLDINGS, located in Qianhai, China, is a new real-estate project operator, structuring urban-rural real-estate investment and development, and industrial fund investment. The company also invests in supply chain management and supporting infrastructures. To create new spaces and livable cities Vensol Holdings develop win-win strategic partnerships with a number of institutions. Currently cooperating with Tianjing North Lumore, China urban and rural integrated demonstration.</p>
</section>

<section class="works abs" role="img" aria-label="Dim background photo of a businessman in a suit">
  <h2 class="section-title abs">Our Works</h2>
  <p class="works-intro abs">VENSOL HOLDINGS, located in Qianhai, China, is a new real-estate project operator, structuring urban-rural real-estate investment and development, and industrial fund investment.</p>
  <div class="works-rule abs"></div>
  <div class="works-frame abs">
    <div class="works-photo" role="img" aria-label="Rendering of modern glass towers beside a waterfront"></div>
  </div>
  <svg class="slide-arrow abs" style="left:111px;top:185px" viewBox="0 0 14 16"><path d="M8 5 L5 8 L8 11" fill="none" stroke="#aaa" stroke-width="1"/></svg>
  <svg class="slide-arrow abs" style="left:366px;top:185px" viewBox="0 0 14 16"><path d="M6 5 L9 8 L6 11" fill="none" stroke="#aaa" stroke-width="1"/></svg>
  <h3 class="works-heading abs">Industrial fund investment</h3>
  <p class="works-copy abs">VENSOL HOLDINGS, located in Qianhai, China, is a new real-estate project operator, structuring urban-rural real-estate investment and development, and industrial fund investment. The company also invests in supply chain management and supporting infrastructures. To create new spaces and livable cities Vensol Holdings develop win-win strategic partnerships with a number of institutions. Currently cooperating with Tianjing North Lumore, China urban and rural integrated demonstration.</p>
  <div class="outline-button abs">View More our Work</div>
</section>

<section class="feeds abs">
  <div class="feed-icon abs"></div>
  <h2 class="section-title abs">Chirper Feeds</h2>
  <svg class="feed-arrow abs" style="left:98px" viewBox="0 0 18 18"><path d="M10 6 L7 9 L10 12" fill="none" stroke="#bbb" stroke-width="1"/></svg>
  <svg class="feed-arrow abs" style="left:597px" viewBox="0 0 18 18"><path d="M8 6 L11 9 L8 12" fill="none" stroke="#bbb" stroke-width="1"/></svg>
  <p class="feeds-copy abs">VENSOL HOLDINGS, located in Qianhai, China, is a new real-estate project operator, structuring urban-rural real-estate investment and development, and industrial fund investment.</p>
  <p class="feeds-link abs">http//www.vensolfeed.com/index</p>
</section>

<footer class="site-footer abs">
  <h4 class="footer-title abs" style="left:107px">About Us</h4>
  <p class="footer-copy abs" style="left:107px;top:35px;width:150px">VENSOL HOLDINGS, located in Qianhai, China, is a new real-estate project operator, structuring urban-rural real-estate investment and development, and industrial fund investment.</p>
  <p class="footer-copy abs" style="left:107px;top:87px;width:150px">The company also invests in supply chain management and supporting infrastructures. urban and rural integrated demonstration.</p>

  <h4 class="footer-title abs" style="left:301px">Services</h4>
  <ul class="service-list abs">
    <li>Real-estate project operator</li>
    <li>Structuring urban-rural real-estate investment</li>
    <li>Development, and industrial fund investment</li>
    <li>Chain management and supporting infrastructures</li>
  </ul>

  <h4 class="footer-title abs" style="left:468px">Contact Us</h4>
  <div class="field abs" style="top:35px;height:16px">Name :</div>
  <div class="field abs" style="top:55px;height:16px">Email :</div>
  <div class="field abs" style="top:75px;height:28px">Message :</div>
  <div class="submit abs">Submit</div>
</footer>

<div class="base-bar abs">
  <p class="copyright abs">Copyrights @2013. Media co. All Rights Reserved</p>
  <span class="social abs" style="left:546px"></span>
  <span class="social abs" style="left:561px"></span>
  <span class="social abs" style="left:577px"></span>
  <span class="social abs" style="left:592px"></span>
  <span class="base-code abs">C8</span>
</div>

</body>
</html>
```